Website homepage rework for women's travel website

I have a homepage (http://www.ladies-at-the-helm.com) that I'm 50% happy with but don't want to completely overhaul. I'd like to retain a similar look but upgrade it to something a bit more modern and less old-fashioned. The basic sense of the site is empowering, self-confident, fun and adventurous - but female and over 40.

A number of the elements on the page have to be redesigned, a few can be tweaked, and a few left alone. See the rest of the brief for further information.

Target Market(s)

women over 40 who like to travel

Industry/Entity Type

Travel

Number of Pages Required

1 page

Font styles to use
Other font styles liked:
• see my brief

Requirements
Must have
• - size - the page must be significantly wider
• - the only font I MUST keep is Raleway (as in the tagline) and possibly the font of the site name (Ladies at the Helm). Both of those work for me. There are too many fonts on the page, however, and that needs to be unified.
• - the rectangles I click to get inside the site have to change to something more modern, possibly square - they do not have to be separated into two columns as they are now, nor do they need the titles (toolkit etc)
• - I like the background image of the header - but it needs to be wider of course - also keep in mind the aspect - it has to fit into the smaller inside pages, whose size will not change
• - at the end of the project I need to receive the separate elements of the design so I can eventually make a change myself if needed ie. replace my own photo, for example
Nice to have
• - the three photos need to change to something more eye-popping - or something else should take their place to fill the space
Should not have
• I do not want a full, original redesign. I want my readers to still feel as though they are on the same site - same header, mostly same fonts.

```html
<!DOCTYPE html>
<html lang="en">
<head>
<meta charset="utf-8">
<title>Ladies at the Helm</title>
<link href="https://fonts.googleapis.com/css2?family=Raleway:wght@300;400;500;700;800&display=swap" rel="stylesheet">
<style>
:root{
  --ink:#1f1f1f;
  --nav:#1e1e1e;
  --band:#332c29;
  --orange:#e8891a;
  --orange-deep:#d9480f;
  --text:#333;
  --muted:#666;
  --red:#d0261c;
  --blue:#31a6d6;
  --amber:#e98b0c;
  --green:#52a22a;
  --pink:#e45867;
  --cyan:#3cc7ee;
  --white:#fff;
}
*{box-sizing:border-box;margin:0;padding:0}
html,body{width:679px;height:1200px;overflow:hidden}
body{font-family:'Raleway',sans-serif;color:var(--text);background:var(--white);position:relative}
.site-nav{height:70px;background:var(--nav);display:flex;align-items:center;gap:24px;padding-left:56px}
.site-nav a{color:var(--white);text-decoration:none;font-size:13.5px;font-weight:400;letter-spacing:.2px}
.hero{position:relative;height:307px;overflow:hidden}
.hero-scene{position:absolute;inset:0;background:linear-gradient(180deg,#c76a14 0%,#e7a23b 30%,#b9732f 48%,#6f5a44 62%,#4d4843 100%)}
.host-photo{position:absolute;left:72px;top:118px;width:218px;height:189px;border-radius:90px 90px 0 0;background:linear-gradient(180deg,#d9c79a 0%,#c9b79a 45%,#b8b29e 100%)}
.brand-disc{position:absolute;left:272px;top:-70px;width:328px;height:328px;border-radius:50%;background:rgba(255,255,255,.93);text-align:center}
.brand-name{margin-top:144px;font-size:29px;font-weight:700;color:var(--orange-deep)}
.brand-tagline{font-size:13px;color:var(--ink);margin-top:2px}
.snapshots{display:flex;justify-content:center;gap:6px;margin-top:14px}
.snapshot{width:78px;height:72px;background:var(--white);padding:4px;box-shadow:0 1px 3px rgba(0,0,0,.3)}
.snapshot div{width:100%;height:100%}
.snap-1{transform:rotate(-4deg)}.snap-1 div{background:linear-gradient(#6cb6e4,#2f6f95)}
.snap-2{transform:rotate(3deg)}.snap-2 div{background:linear-gradient(#e59a3a,#2f8bc5)}
.snap-3{transform:rotate(-2deg)}.snap-3 div{background:linear-gradient(#a8825a,#6b8a4e)}
.intro{height:186px;text-align:center;padding-top:31px}
.intro h1{font-size:18.5px;font-weight:400;line-height:27px;color:var(--ink);width:500px;margin:0 auto}
.pillars{list-style:none;text-align:left;width:360px;margin:14px auto 0}
.pillars li{font-size:10.5px;line-height:19px;color:var(--muted);display:flex;align-items:center;gap:5px}
.pillars b{color:var(--ink);font-weight:500}
.call-band{height:160px;background:var(--band);text-align:center;padding-top:38px}
.call-band h2{font-size:38px;font-weight:300;color:var(--white)}
.call-band p{font-size:21px;color:var(--orange);margin-top:2px}
.call-band a{color:var(--orange)}
.section{position:relative;height:225px;text-align:center;padding-top:18px}
.section h3{font-size:23px;font-weight:400;color:var(--ink);display:inline-block;padding-bottom:4px;border-bottom:1px solid #ddd}
.destinations{height:212px;background:linear-gradient(180deg,#4a3f36,#3a342e 60%,#2f2b28)}
.destinations h3{color:var(--white);border-color:#777}
.pager{position:absolute;right:56px;top:42px;display:flex;gap:3px}
.pager span{width:16px;height:16px;border-radius:50%;background:#ddd;display:flex;align-items:center;justify-content:center}
.destinations .pager{top:40px}
.destinations .pager span{background:var(--white)}
.cards{display:flex;gap:16px;margin:22px 0 0 56px}
.destinations .cards{margin-top:22px}
.card{width:179px;height:104px;position:relative;text-align:left;overflow:hidden}
.card-art{position:absolute;inset:0}
.card-head{position:absolute;left:0;top:0;width:100%;height:40px;padding:5px 10px;color:var(--white)}
.card-head strong{display:block;font-size:13px;font-weight:800;text-transform:uppercase}
.card-head span{display:block;font-size:9.5px;font-weight:400;margin-top:1px}
.c-red{background:var(--red)}.c-blue{background:var(--blue)}.c-amber{background:var(--amber)}
.c-green{background:var(--green)}.c-pink{background:var(--pink)}.c-cyan{background:var(--cyan)}
.site-footer{position:absolute;left:0;bottom:0;width:100%;height:40px;background:var(--nav);display:flex;align-items:center;padding:0 56px;font-size:8px;color:#ddd}
.social{margin-left:auto;display:flex;align-items:center;gap:6px}
.social i{width:15px;height:15px;border-radius:50%;display:block}
</style>
</head>
<body>
<nav class="site-nav">
  <a href="#">START HERE</a><a href="#">ABOUT</a><a href="#">TRAVEL RESOURCES</a><a href="#">BLOG</a><a href="#">TRAVEL SHOP</a><a href="#">CONTACT</a>
</nav>

<header class="hero">
  <div class="hero-scene" role="img" aria-label="Desert road stretching toward red mesas under an orange sky"></div>
  <div class="host-photo" role="img" aria-label="Portrait of the site's author, smiling, sunglasses on her head"></div>
  <div class="brand-disc">
    <div class="brand-name">Ladies at the Helm</div>
    <div class="brand-tagline">For women who travel smart, safe + solo</div>
    <div class="snapshots">
      <div class="snapshot snap-1"><div role="img" aria-label="Tropical beach with palm trees"></div></div>
      <div class="snapshot snap-2"><div role="img" aria-label="Blue pots with succulent plants"></div></div>
      <div class="snapshot snap-3"><div role="img" aria-label="Scooter parked in a sunny street"></div></div>
    </div>
  </div>
</header>

<section class="intro">
  <h1>Hi, I'm Marla. I took my first solo trip at 15. I'll show you how to travel...</h1>
  <ul class="pillars">
    <li><svg width="10" height="10" viewBox="0 0 10 10"><circle cx="5" cy="5" r="5" fill="#e8891a"/><path d="M2.7 5.1l1.6 1.6 3-3.2" stroke="#fff" stroke-width="1.3" fill="none"/></svg><span><b>Smart:</b> practical tools to help you plan – and afford – the perfect trip</span></li>
    <li><svg width="10" height="10" viewBox="0 0 10 10"><circle cx="5" cy="5" r="5" fill="#e8891a"/><path d="M2.7 5.1l1.6 1.6 3-3.2" stroke="#fff" stroke-width="1.3" fill="none"/></svg><span><b>Safe:</b> down-to-earth advice and a ton of safety recommendations</span></li>
    <li><svg width="10" height="10" viewBox="0 0 10 10"><circle cx="5" cy="5" r="5" fill="#e8891a"/><path d="M2.7 5.1l1.6 1.6 3-3.2" stroke="#fff" stroke-width="1.3" fill="none"/></svg><span><b>Solo:</b> yes, you can do it!</span></li>
  </ul>
</section>

<section class="call-band">
  <h2>Thinking of solo travel?</h2>
  <p><a href="#">CLICK HERE</a> to find out how.</p>
</section>

<section class="section toolkit">
  <h3>Travel Toolkit</h3>
  <div class="pager"><span><svg width="6" height="6" viewBox="0 0 6 6"><path d="M4 1L2 3l2 2" stroke="#666" fill="none"/></svg></span><span><svg width="6" height="6" viewBox="0 0 6 6"><path d="M2 1l2 2-2 2" stroke="#666" fill="none"/></svg></span></div>
  <div class="cards">
    <article class="card"><div class="card-art" role="img" aria-label="Plate of smoked salmon and olives" style="background:linear-gradient(#f4ede4,#e6c9a4)"></div><div class="card-head c-red"><strong>Eating with Locals</strong><span>The Ultimate Guide to Social Dining</span></div></article>
    <article class="card"><div class="card-art" role="img" aria-label="Open suitcase packed with clothes and sandals" style="background:linear-gradient(#3a3f58,#2c3656)"></div><div class="card-head c-blue"><strong>Your Packing List</strong><span>Take what you need - no more</span></div></article>
    <article class="card"><div class="card-art" role="img" aria-label="Sunset over mossy green hills" style="background:linear-gradient(#e0a640,#566b23 55%,#2f3a16)"></div><div class="card-head c-amber"><strong>No Single Supplement</strong><span>17 ways to avoid paying it</span></div></article>
  </div>
</section>

<section class="section destinations">
  <h3>Destinations</h3>
  <div class="pager"><span><svg width="6" height="6" viewBox="0 0 6 6"><path d="M4 1L2 3l2 2" stroke="#333" fill="none"/></svg></span><span><svg width="6" height="6" viewBox="0 0 6 6"><path d="M2 1l2 2-2 2" stroke="#333" fill="none"/></svg></span></div>
  <div class="cards">
    <article class="card"><div class="card-art" role="img" aria-label="Lake framed by pine trees" style="background:linear-gradient(#6aa9df,#2f6196 50%,#2a4a22)"></div><div class="card-head c-green"><strong>Solo in Argentina</strong><span>Does it really take two to tango?</span></div></article>
    <article class="card"><div class="card-art" role="img" aria-label="Plate of saffron risotto" style="background:linear-gradient(#c9c0b8,#f2c62c 60%,#e8e1d9)"></div><div class="card-head c-pink"><strong>Europe for Foodies</strong><span>9 top destinations to try in October</span></div></article>
    <article class="card"><div class="card-art" role="img" aria-label="Family on a sunny beach with inflatables" style="background:linear-gradient(#8fd8f4,#2fb2e0 55%,#e8dcc0)"></div><div class="card-head c-cyan"><strong>Rebellious Carouge</strong><span>Geneva's Alter Ego?</span></div></article>
  </div>
</section>

<footer class="site-footer">
  <span>© 2016 LADIES-AT-THE-HELM. All Rights Reserved.</span>
  <div class="social"><span>Connect Us On:</span><i style="background:#3b5998"></i><i style="background:#2a9fd8"></i><i style="background:#e0405a"></i><i style="background:#1d6aa8"></i></div>
</footer>
</body>
</html>
```